Redesign Website - Current one too plain

The description is in the uploaded file. Please let me know if you need any more information. I'd prefer it if someone could implement the design to a WordPress site but the best design will win, regardless.
I would like the forms to look nice as well
UPDATE:
I don't think we can use the images that I provided, I think they make the site look a bit 'cheap' and I really don't know how to replace them. One thought I have had is to make the "Simple, Unique, Effective" a second feature on the right side of the page with the search on the left
Target Market(s)
Small companies, private sellers of cars and people who rent their caravan/holiday home out
Industry/Entity Type
Advertising
Number of Pages Required
3 page
Colors
Designer to choose colors to be used in the design.
Look and feel
Each slider illustrates characteristics of the customer's brand and the style your logo design should communicate.

```html
<!DOCTYPE html>
<html lang="en">
<head>
<meta charset="utf-8">
<title>Contact Us – Trovix</title>
<link rel="stylesheet" href="https://fonts.googleapis.com/css2?family=Outfit:wght@300;400;500;600;700&display=swap">
<style>
  :root {
    --ink: #111111;
    --nav-bg: #111111;
    --white: #ffffff;
    --accent: #e2ff13;
    --field: #f7f4f5;
    --placeholder: #a9a4a6;
    --photo-road-a: #1c2a14;
    --photo-road-b: #3e4a35;
    --photo-road-c: #2a2b2c;
    --photo-car-a: #2b2d33;
    --photo-car-b: #8a8f96;
    --photo-car-c: #5a4536;
  }
  * { box-sizing: border-box; margin: 0; padding: 0; }
  html, body {
    width: 1200px; height: 1090px; overflow: hidden;
    background: var(--white);
    font-family: "Outfit", sans-serif;
    color: var(--ink);
  }
  .page { position: relative; width: 1200px; height: 1090px; }

  .site-nav {
    position: absolute; left: 21px; top: 22px; width: 1159px; height: 75px;
    background: var(--nav-bg); border-radius: 16px;
  }
  .brand {
    position: absolute; left: 52px; top: 0; height: 75px;
    display: flex; align-items: center; gap: 9px;
    color: var(--accent); font-size: 22px; font-weight: 400; letter-spacing: 2.5px;
  }
  .brand-dot { width: 16px; height: 16px; border-radius: 50%; background: var(--accent); }
  .nav-links {
    position: absolute; left: 450px; top: 0; height: 75px;
    display: flex; align-items: center; gap: 20px; list-style: none;
  }
  .nav-links a { color: var(--white); text-decoration: none; font-size: 14px; font-weight: 400; }
  .nav-links a.is-active { color: var(--accent); font-weight: 500; }
  .login-btn {
    position: absolute; left: 982px; top: 17px; width: 130px; height: 41px;
    border: 1px solid var(--white); border-radius: 21px;
    color: var(--white); font-size: 14px; font-weight: 400;
    display: flex; align-items: center; justify-content: center; text-decoration: none;
  }

  .hero-photo {
    position: absolute; left: 21px; top: 107px; width: 1159px; height: 281px;
    border-radius: 16px;
    background: linear-gradient(100deg, var(--photo-road-a) 0%, var(--photo-road-b) 35%, var(--photo-road-c) 65%, var(--photo-road-a) 100%);
  }

  .contact-form { position: absolute; left: 0; top: 0; width: 0; height: 0; }
  .contact-title {
    position: absolute; left: 161px; top: 436px;
    font-size: 33px; font-weight: 400; line-height: 38px; white-space: nowrap;
  }
  .contact-title strong { font-weight: 700; }
  .field-label {
    position: absolute; left: 161px;
    font-size: 17px; font-weight: 400; line-height: 22px; white-space: nowrap;
  }
  .label-name { top: 500px; }
  .label-email { top: 616px; }
  .label-msg { top: 730px; }
  .field {
    position: absolute; left: 161px; width: 446px; height: 56px; border: 0; border-radius: 14px;
    background: var(--field); padding: 0 35px;
    font-family: "Outfit", sans-serif; font-size: 13px; font-weight: 300; color: var(--ink);
  }
  .field::placeholder { color: var(--placeholder); }
  .field-name { top: 539px; }
  .field-email { top: 655px; }
  textarea.field { top: 769px; height: 142px; padding-top: 17px; resize: none; line-height: 18px; }
  .submit-btn {
    position: absolute; left: 163px; top: 946px;
    display: flex; align-items: center; justify-content: space-between;
    width: 156px; height: 42px; border: 0; border-radius: 21px;
    background: var(--accent); padding: 0 20px 0 34px;
    font-family: "Outfit", sans-serif; font-size: 15px; font-weight: 500; color: var(--ink);
  }

  .driver-photo {
    position: absolute; left: 641px; top: 434px; width: 539px; height: 575px;
    border-radius: 12px;
    background: linear-gradient(135deg, var(--photo-car-b) 0%, var(--photo-car-a) 30%, var(--photo-car-c) 60%, var(--photo-car-a) 100%);
  }

  .site-footer {
    position: absolute; left: 161px; top: 1043px; width: 876px;
    display: flex; justify-content: space-between; font-size: 14.5px; font-weight: 300;
  }
  .site-footer strong { font-weight: 700; }
  .legal-links a { color: var(--ink); text-decoration: none; font-weight: 400; }
  .legal-links span { margin: 0 6px; }
</style>
</head>
<body>
<div class="page">
  <header class="site-nav">
    <div class="brand"><span class="brand-dot"></span>TROVIX</div>
    <ul class="nav-links">
      <li><a href="#">Home</a></li>
      <li><a href="#">Advertise</a></li>
      <li><a href="#" class="is-active">Contact</a></li>
      <li><a href="#">Register</a></li>
    </ul>
    <a href="#" class="login-btn">LOGIN</a>
  </header>

  <div class="hero-photo" role="img" aria-label="Silver sports car driving fast on a winding forest road"></div>

  <form class="contact-form">
    <h1 class="contact-title">Contact <strong>Us</strong></h1>
    <label class="field-label label-name" for="name">Full Name</label>
    <input class="field field-name" id="name" type="text" placeholder="Enter Your Full Name.">
    <label class="field-label label-email" for="email">Email Address</label>
    <input class="field field-email" id="email" type="email" placeholder="Enter Your Email Address.">
    <label class="field-label label-msg" for="msg">Message</label>
    <textarea class="field" id="msg" placeholder="Enter Your Message"></textarea>
    <button class="submit-btn" type="button">Submit
      <svg width="22" height="16" viewBox="0 0 22 16" fill="none" stroke="#111" stroke-width="2" stroke-linecap="round" stroke-linejoin="round"><path d="M1 8h19M13 1l7 7-7 7"/></svg>
    </button>
  </form>

  <div class="driver-photo" role="img" aria-label="Smiling man in a suit sitting at the wheel of a dark car"></div>

  <footer class="site-footer">
    <p>© 2023 <strong>TROVIX.</strong> All rights reserved.</p>
    <p class="legal-links"><a href="#">Terms &amp; Conditions</a><span>|</span><a href="#">Privacy Policy</a></p>
  </footer>
</div>
</body>
</html>
```